Tollin Waste Website Design

Our new start-up needs a website design. We plan to help businesses find more sustainable ways to manage their waste. Our initial website aims to gather contact data from potential business customers and comprehensive information from waste facilities and waste transporters. We have a logo design (attached) which we would like included in the website design. I have also attached a number of pages that describe what information should appear on each page as well as a web design brief file that describes the look we are after.

```html
<!DOCTYPE html>
<html lang="en">
<head>
<meta charset="utf-8">
<title>Tollin Waste – Website Design</title>
<link href="https://fonts.googleapis.com/css2?family=Montserrat:wght@400;500;600;700;800&family=Open+Sans:wght@400;600;700&display=swap" rel="stylesheet">
<style>
:root{
  --board:#e3e3e6;
  --green:#9bca2b;
  --green-deep:#5f9a22;
  --green-btn:#4e8f1f;
  --green-glass:rgba(104,170,40,.86);
  --ink:#1d1d1d;
  --ink-soft:#2f3a1a;
  --white:#ffffff;
  --dark-tile:rgba(30,30,30,.78);
}
*{box-sizing:border-box;margin:0;padding:0}
html,body{width:1200px;height:2744px;overflow:hidden}
body{background:var(--board);position:relative;font-family:"Open Sans",sans-serif;color:var(--ink)}
.screen{position:absolute;left:46px;width:1123px;height:1206px;background:var(--white);overflow:hidden}
.screen--home{top:40px}
.screen--signup{top:1395px}
.hero{position:absolute;left:0;top:0;width:1123px;height:640px;
  background:linear-gradient(180deg,#9fb7cf 0%,#c9d3db 22%,#8c8a80 45%,#77756d 70%,#a8a49a 100%)}
.brand{position:absolute;left:122px;top:46px;display:flex;align-items:center;gap:14px;white-space:nowrap}
.brand__dot{flex:none;width:64px;height:64px;border-radius:50%;background:var(--green)}
.brand__name{font-family:"Montserrat",sans-serif;font-weight:700;font-size:36px;letter-spacing:1px;color:#3a3a3a}
.nav{position:absolute;top:30px;left:618px}
.nav a{font-family:"Montserrat",sans-serif;font-size:13px;font-weight:500;color:var(--ink);text-decoration:none;position:absolute;white-space:nowrap}
.welcome{position:absolute;left:133px;top:258px;width:342px;height:165px;background:var(--green-glass);color:var(--white);padding:25px 0 0 32px;font-family:"Montserrat",sans-serif}
.welcome__kicker{font-size:18px;font-weight:700;line-height:1}
.welcome__title{font-size:30px;font-weight:700;line-height:1.15;margin-top:4px}
.welcome__lead{font-size:22px;font-weight:400;line-height:1.1;margin-top:12px;padding-left:4px}
.welcome__lead b{font-weight:700}
.slide-arrow{position:absolute;top:304px;width:36px;height:40px;background:var(--dark-tile);display:flex;align-items:center;justify-content:center}
.slide-arrow--prev{left:0}
.slide-arrow--next{right:0}
.card{position:absolute;top:567px;width:296px;height:242px;background:var(--white);padding:7px;box-shadow:0 2px 6px rgba(0,0,0,.2)}
.card__photo{width:100%;height:210px}
.card__label{position:absolute;left:26px;bottom:-25px;width:232px;height:38px;background:var(--green);color:var(--white);white-space:nowrap;
  font-family:"Montserrat",sans-serif;font-weight:700;font-size:16px;display:flex;align-items:center;padding-left:14px;box-shadow:0 2px 4px rgba(0,0,0,.2)}
.card--transporters .card__label{width:256px}
.card__go{position:absolute;right:-10px;top:8px;width:22px;height:22px;border-radius:50%;background:var(--green-deep);display:flex;align-items:center;justify-content:center}
.card--producers{left:100px}.card--facilities{left:411px}.card--transporters{left:728px}
.photo-producers{background:linear-gradient(160deg,#4a6a8a,#9ea3a8 55%,#d7d3cb)}
.photo-facilities{background:linear-gradient(160deg,#6b6f74,#c9c4b8 50%,#5b6b3d)}
.photo-transporters{background:linear-gradient(160deg,#b8c3cf,#8a8f96 45%,#b77e72 75%,#d8d6d2)}
.footer{position:absolute;left:0;top:869px;width:1123px;height:337px;background:var(--green);border-top:4px solid #6aa11c}
.footer .brand{left:122px;top:84px;gap:12px}
.footer .brand__dot{background:var(--white);width:62px;height:62px}
.footer .brand__name{color:var(--white);font-size:30px}
.footer__col{position:absolute;top:58px;font-size:11px;color:var(--ink-soft);line-height:1.45}
.footer__col h4{font-family:"Montserrat",sans-serif;font-size:12px;font-weight:600;color:var(--ink);margin-bottom:18px}
.footer__col--contact{left:503px}
.footer__col--menu{left:722px}
.footer__col--social{left:876px}
.contact-row{display:flex;gap:12px;margin-bottom:14px}
.contact-row svg{flex:none;margin-top:2px}
.footer__col--menu a{display:block;color:var(--ink-soft);text-decoration:none;line-height:1.5}
.social-row{display:flex;align-items:center;gap:12px;margin-bottom:12px}
.social-row span.dot{width:26px;height:26px;border-radius:50%;background:#27425f}
.footer__rule{position:absolute;left:122px;right:48px;top:251px;height:1px;background:rgba(255,255,255,.45)}
.footer__copy{position:absolute;left:0;width:100%;top:301px;text-align:center;font-size:11px;color:var(--ink-soft)}
.dim{position:absolute;inset:0;background:rgba(0,0,0,.62)}
.modal{position:absolute;left:342px;top:329px;width:446px;height:406px;background:var(--white)}
.modal__badge{position:absolute;left:166px;top:-121px;width:128px;height:128px;border-radius:50%;background:var(--white);display:flex;align-items:center;justify-content:center}
.modal__badge span{width:72px;height:72px;border-radius:50%;background:var(--green)}
.modal__close{position:absolute;right:13px;top:14px;width:28px;height:28px;border-radius:50%;background:var(--green-btn);display:flex;align-items:center;justify-content:center}
.modal__text{position:absolute;top:88px;left:40px;right:40px;text-align:center;font-weight:600;font-size:19.5px;line-height:1.3;color:#111;text-transform:uppercase}
.modal__field{position:absolute;left:40px;top:227px;width:362px;height:46px;border:1px solid #9a9a9a;display:flex;align-items:center;gap:12px;padding-left:16px;font-size:13px;color:#222}
.modal__submit{position:absolute;left:143px;top:313px;width:150px;height:46px;background:var(--green-btn);color:var(--white);border:none;
  font-family:"Montserrat",sans-serif;font-weight:800;font-size:19px;display:flex;align-items:center;justify-content:center}
</style>
</head>
<body>

<section class="screen screen--home">
  <div class="hero" role="img" aria-label="Photo of a truck loaded with baled recyclable plastic in a waste yard"></div>
  <div class="brand"><span class="brand__dot"></span><span class="brand__name">TOLLIN WASTE</span></div>
  <nav class="nav">
    <a style="left:0">About us</a><a style="left:95px">What we do</a><a style="left:208px">Resources</a><a style="left:312px">Contact us</a>
  </nav>
  <div class="welcome">
    <div class="welcome__kicker">WELCOME TO</div>
    <div class="welcome__title">TOLLIN WASTE</div>
    <div class="welcome__lead">Take a control of your<br><b>waste</b> here</div>
  </div>
  <div class="slide-arrow slide-arrow--prev"><svg width="12" height="14" viewBox="0 0 12 14"><path d="M9 1 3 7l6 6" fill="none" stroke="#fff" stroke-width="2.5"/></svg></div>
  <div class="slide-arrow slide-arrow--next"><svg width="12" height="14" viewBox="0 0 12 14"><path d="M3 1l6 6-6 6" fill="none" stroke="#fff" stroke-width="2.5"/></svg></div>

  <div class="card card--producers"><div class="card__photo photo-producers" role="img" aria-label="Photo of a conveyor feeding paper waste into a container"></div>
    <div class="card__label">WASTE PRODUCERS<span class="card__go"><svg width="8" height="10" viewBox="0 0 8 10"><path d="M2 1l4 4-4 4" fill="none" stroke="#fff" stroke-width="2"/></svg></span></div></div>
  <div class="card card--facilities"><div class="card__photo photo-facilities" role="img" aria-label="Photo of a recycling facility sorting line"></div>
    <div class="card__label">WASTE FACILITIES<span class="card__go"><svg width="8" height="10" viewBox="0 0 8 10"><path d="M2 1l4 4-4 4" fill="none" stroke="#fff" stroke-width="2"/></svg></span></div></div>
  <div class="card card--transporters"><div class="card__photo photo-transporters" role="img" aria-label="Photo of a truck carrying compacted recyclables"></div>
    <div class="card__label">WASTE TRANSPORTERS<span class="card__go"><svg width="8" height="10" viewBox="0 0 8 10"><path d="M2 1l4 4-4 4" fill="none" stroke="#fff" stroke-width="2"/></svg></span></div></div>

  <footer class="footer">
    <div class="brand"><span class="brand__dot"></span><span class="brand__name">TOLLIN WASTE</span></div>
    <div class="footer__col footer__col--contact">
      <h4>CONTACT US</h4>
      <div class="contact-row"><svg width="9" height="12" viewBox="0 0 9 12"><path d="M4.5 0A4.5 4.5 0 0 0 0 4.5C0 8 4.5 12 4.5 12S9 8 9 4.5A4.5 4.5 0 0 0 4.5 0zm0 6.3a1.8 1.8 0 1 1 0-3.6 1.8 1.8 0 0 1 0 3.6z" fill="#222"/></svg><span>418 Commerce Way<br>Lindale, IL 60400</span></div>
      <div class="contact-row"><svg width="11" height="11" viewBox="0 0 11 11"><path d="M2.2 0 4 2.6 2.9 4a7 7 0 0 0 4.1 4.1L8.4 7 11 8.8 9.6 11C4.5 11 0 6.5 0 1.4z" fill="#222"/></svg><span>555.014.2290</span></div>
      <div class="contact-row"><svg width="12" height="9" viewBox="0 0 12 9"><path d="M0 0h12v9H0z" fill="#222"/><path d="M0 0l6 5 6-5" fill="none" stroke="#9bca2b" stroke-width="1.2"/></svg><span>info@tollinwaste.com</span></div>
    </div>
    <div class="footer__col footer__col--menu">
      <h4>MENU</h4>
      <a>About us</a><a>What we do</a><a>Resources</a><a>Contact us</a>
    </div>
    <div class="footer__col footer__col--social">
      <h4>CONNECT WITH US</h4>
      <div class="social-row"><span class="dot"></span>Community</div>
      <div class="social-row"><span class="dot"></span>Updates</div>
      <div class="social-row"><span class="dot"></span>Network</div>
    </div>
    <div class="footer__rule"></div>
    <div class="footer__copy">Copyrights @ 2018 All Rights Reserved</div>
  </footer>
</section>

<section class="screen screen--signup">
  <div class="hero" role="img" aria-label="Photo of a truck loaded with baled recyclable plastic in a waste yard"></div>
  <div class="brand"><span class="brand__dot"></span><span class="brand__name">TOLLIN WASTE</span></div>
  <nav class="nav">
    <a style="left:0">About us</a><a style="left:95px">What we do</a><a style="left:208px">Resources</a><a style="left:312px">Contact us</a>
  </nav>
  <div class="welcome">
    <div class="welcome__kicker">WELCOME TO</div>
    <div class="welcome__title">TOLLIN WASTE</div>
    <div class="welcome__lead">Take a control of your<br><b>waste</b> here</div>
  </div>
  <div class="slide-arrow slide-arrow--prev"><svg width="12" height="14" viewBox="0 0 12 14"><path d="M9 1 3 7l6 6" fill="none" stroke="#fff" stroke-width="2.5"/></svg></div>
  <div class="slide-arrow slide-arrow--next"><svg width="12" height="14" viewBox="0 0 12 14"><path d="M3 1l6 6-6 6" fill="none" stroke="#fff" stroke-width="2.5"/></svg></div>

  <div class="card card--producers"><div class="card__photo photo-producers" role="img" aria-label="Photo of a conveyor feeding paper waste into a container"></div>
    <div class="card__label">WASTE PRODUCERS<span class="card__go"><svg width="8" height="10" viewBox="0 0 8 10"><path d="M2 1l4 4-4 4" fill="none" stroke="#fff" stroke-width="2"/></svg></span></div></div>
  <div class="card card--facilities"><div class="card__photo photo-facilities" role="img" aria-label="Photo of a recycling facility sorting line"></div>
    <div class="card__label">WASTE FACILITIES<span class="card__go"><svg width="8" height="10" viewBox="0 0 8 10"><path d="M2 1l4 4-4 4" fill="none" stroke="#fff" stroke-width="2"/></svg></span></div></div>
  <div class="card card--transporters"><div class="card__photo photo-transporters" role="img" aria-label="Photo of a truck carrying compacted recyclables"></div>
    <div class="card__label">WASTE TRANSPORTERS<span class="card__go"><svg width="8" height="10" viewBox="0 0 8 10"><path d="M2 1l4 4-4 4" fill="none" stroke="#fff" stroke-width="2"/></svg></span></div></div>

  <footer class="footer">
    <div class="brand"><span class="brand__dot"></span><span class="brand__name">TOLLIN WASTE</span></div>
    <div class="footer__col footer__col--contact">
      <h4>CONTACT US</h4>
      <div class="contact-row"><svg width="9" height="12" viewBox="0 0 9 12"><path d="M4.5 0A4.5 4.5 0 0 0 0 4.5C0 8 4.5 12 4.5 12S9 8 9 4.5A4.5 4.5 0 0 0 4.5 0zm0 6.3a1.8 1.8 0 1 1 0-3.6 1.8 1.8 0 0 1 0 3.6z" fill="#222"/></svg><span>418 Commerce Way<br>Lindale, IL 60400</span></div>
      <div class="contact-row"><svg width="11" height="11" viewBox="0 0 11 11"><path d="M2.2 0 4 2.6 2.9 4a7 7 0 0 0 4.1 4.1L8.4 7 11 8.8 9.6 11C4.5 11 0 6.5 0 1.4z" fill="#222"/></svg><span>555.014.2290</span></div>
      <div class="contact-row"><svg width="12" height="9" viewBox="0 0 12 9"><path d="M0 0h12v9H0z" fill="#222"/><path d="M0 0l6 5 6-5" fill="none" stroke="#9bca2b" stroke-width="1.2"/></svg><span>info@tollinwaste.com</span></div>
    </div>
    <div class="footer__col footer__col--menu">
      <h4>MENU</h4>
      <a>About us</a><a>What we do</a><a>Resources</a><a>Contact us</a>
    </div>
    <div class="footer__col footer__col--social">
      <h4>CONNECT WITH US</h4>
      <div class="social-row"><span class="dot"></span>Community</div>
      <div class="social-row"><span class="dot"></span>Updates</div>
      <div class="social-row"><span class="dot"></span>Network</div>
    </div>
    <div class="footer__rule"></div>
    <div class="footer__copy">Copyrights @ 2018 All Rights Reserved</div>
  </footer>

  <div class="dim"></div>
  <div class="modal" role="dialog" aria-label="Sign up for updates">
    <div class="modal__badge"><span></span></div>
    <div class="modal__close"><svg width="12" height="12" viewBox="0 0 12 12"><path d="M2 2l8 8M10 2l-8 8" stroke="#fff" stroke-width="2.4"/></svg></div>
    <p class="modal__text">Welcome to Tollin Waste. We are just getting started. Please register your email address to receive updates from us.</p>
    <div class="modal__field"><svg width="12" height="9" viewBox="0 0 12 9"><path d="M0 0h12v9H0z" fill="#333"/><path d="M0 0l6 5 6-5" fill="none" stroke="#fff" stroke-width="1.2"/></svg>E Mail id</div>
    <button class="modal__submit">SIGNUP</button>
  </div>
</section>

</body>
</html>
```